Book Cover: Morrow ashes

Creation of a cover for the book "The Ashes of Morrow", 16 x 24 cm. Image available (attached document) Author (top of the cover): "Gérard Lontavel" Title: "The Ashes of Morrow" Other mention: "Preface by Étienne de Vallomire-Dufay" Publisher (Bottom): "Corvane Editions"

Target Market(s)

General public with interest in Geopolitics

Colors

Designer to choose colors to be used in the design.

Requirements
Must have
• Joined image
Nice to have
• -
Should not have
• -

```html
<!DOCTYPE html>
<html lang="en">
<head>
<meta charset="utf-8">
<title>The Ashes of Morrow — Gérard Lontavel</title>
<link rel="stylesheet" href="https://fonts.googleapis.com/css2?family=Bebas+Neue&family=Cinzel:wght@400;500&family=Open+Sans:ital,wght@0,700;1,600&display=swap">
<style>
  :root {
    --backdrop: #d7ecf6;
    --sky: #2fd4ef;
    --sky-deep: #1aa6c2;
    --haze: #6fa8b8;
    --rubble: #9fc0cc;
    --rubble-dark: #2d3f49;
    --band-red: #7a0a12;
    --band-light: #8fb7c6;
    --band-black: #0c0f12;
    --mist: rgba(236, 248, 252, 0.82);
    --ink-white: #ffffff;
    --ink-teal: #1f4450;
  }
  * { margin: 0; padding: 0; box-sizing: border-box; }
  html, body { width: 1200px; height: 1200px; overflow: hidden; }
  body {
    background: radial-gradient(circle at 50% 50%, #eef8fc 0%, var(--backdrop) 70%);
    position: relative;
  }
  .book-cover {
    position: absolute;
    left: 233px; top: 55px;
    width: 737px; height: 1105px;
    overflow: hidden;
    box-shadow: 0 6px 18px rgba(40, 80, 100, 0.35);
  }
  .cover-photo {
    position: absolute; inset: 0;
    background: linear-gradient(180deg,
      var(--sky) 0%, var(--sky-deep) 22%, var(--haze) 45%,
      var(--rubble) 62%, #b9d3dc 72%, #6f8b97 86%, var(--rubble-dark) 100%);
  }
  .flag-bands { position: absolute; inset: 0; width: 737px; height: 1105px; }
  .preface-mist {
    position: absolute;
    left: 0; top: 748px; width: 648px; height: 208px;
    background: var(--mist);
    filter: blur(6px);
  }
  .author {
    position: absolute; top: 68px; left: 0; width: 100%;
    text-align: center;
    font-family: "Open Sans", sans-serif; font-weight: 700;
    font-size: 46px; letter-spacing: -0.5px;
    color: var(--ink-white);
  }
  .title { position: absolute; left: 0; top: 0; width: 100%; height: 100%; color: var(--ink-white); font-weight: 400; }
  .title-small-top {
    position: absolute; left: 0; width: 100%; top: 300px; text-align: center;
    font-family: "Bebas Neue", sans-serif; font-size: 70px; line-height: 1;
    padding-right: 10px;
  }
  .title-main {
    position: absolute; left: 0; width: 100%; top: 372px; text-align: center;
    font-family: "Bebas Neue", sans-serif; font-size: 172px; line-height: 1;
    letter-spacing: 1px;
  }
  .title-link {
    position: absolute; left: 132px; top: 577px;
    font-family: "Cinzel", serif; font-size: 36px; line-height: 1;
  }
  .title-tail {
    position: absolute; left: 206px; top: 522px;
    font-family: "Cinzel", serif; font-weight: 400; font-size: 92px; line-height: 1;
    letter-spacing: -2px;
  }
  .preface {
    position: absolute; left: 0; width: 700px; top: 780px; text-align: center;
    font-family: "Open Sans", sans-serif; font-style: italic; font-weight: 600;
    font-size: 34px; line-height: 1.45;
    color: var(--ink-teal);
  }
  .publisher {
    position: absolute; left: 0; width: 100%; bottom: 44px; text-align: center;
    font-family: "Open Sans", sans-serif; font-weight: 700;
    font-size: 24px; letter-spacing: 1px;
    color: var(--ink-white);
  }
</style>
</head>
<body>
  <main class="book-cover">
    <div class="cover-photo" role="img" aria-label="Blue-tinted photograph of a ruined city street with rubble and passers-by"></div>

    <svg class="flag-bands" viewBox="0 0 737 1105" aria-hidden="true">
      <polygon points="0,280 737,235 737,340 0,390" fill="var(--band-red)" opacity="0.85"/>
      <polygon points="0,390 737,340 737,485 0,535" fill="var(--band-light)" opacity="0.55"/>
      <polygon points="0,535 737,485 737,610 0,650" fill="var(--band-black)" opacity="0.92"/>
      <polygon points="0,650 737,610 737,650 0,690" fill="var(--band-black)" opacity="0.45"/>
    </svg>

    <div class="preface-mist"></div>

    <p class="author">Gérard Lontavel</p>

    <h1 class="title">
      <span class="title-small-top">The</span>
      <span class="title-main">Ashes</span>
      <span class="title-link">OF</span>
      <span class="title-tail">MORROW</span>
    </h1>

    <p class="preface">Preface by Étienne<br>de Vallomire-Dufay</p>

    <p class="publisher">Corvane Editions</p>
  </main>
</body>
</html>
```